Stonebridge Building and Projects business cards

A business card with watermark background (construction work)

Company logo attached

Home improvement projects
House renovations
Bathroom and kitchen renovations
House extensions
New builds and granny flats

Director Omar Haddani
(Phone number)
omar@sbpbuilding.com.au
(Instagram logo) sbp_building

```html
<!DOCTYPE html>
<html lang="en">
<head>
<meta charset="utf-8">
<title>Stonebridge Building and Projects – Business Card</title>
<link rel="stylesheet" href="https://fonts.googleapis.com/css2?family=Montserrat:wght@600&family=Roboto:wght@400;500&display=swap">
<style>
  :root {
    --page-bg: #e4e1dc;
    --card-face: #eef0f1;
    --brand-blue: #1f7fb8;
    --brand-blue-deep: #16689c;
    --edge-dark: #3b3f44;
    --name-blue: #1d5f8c;
    --ink: #3a3d40;
    --icon-ink: #3c4146;
    --white: #ffffff;
  }
  * { margin: 0; padding: 0; box-sizing: border-box; }
  html, body {
    width: 1200px;
    height: 1054px;
    overflow: hidden;
    background: var(--page-bg);
  }
  .canvas {
    position: relative;
    width: 1200px;
    height: 1054px;
  }
  .card {
    position: absolute;
    left: 100px;
    top: 224px;
    width: 1000px;
    height: 605px;
    border-radius: 26px;
    overflow: hidden;
    background: var(--card-face);
    box-shadow: 0 18px 40px rgba(0,0,0,0.18);
  }
  .card__band {
    position: absolute;
    inset: 0;
    width: 1000px;
    height: 605px;
  }
  .brand {
    position: absolute;
    left: 40px;
    top: 210px;
    width: 380px;
    text-align: center;
    color: var(--white);
    font-family: "Montserrat", sans-serif;
    font-weight: 600;
  }
  .brand__mark {
    display: block;
    width: 22px;
    height: 22px;
    margin: 0 auto 22px;
    background: var(--white);
  }
  .brand__name {
    font-size: 40px;
    line-height: 1.15;
  }
  .brand__name span { display: block; }
  .brand__name .brand__sub { font-size: 27px; margin-top: 8px; }
  .contact {
    position: absolute;
    left: 537px;
    top: 168px;
    font-family: "Roboto", sans-serif;
    color: var(--ink);
  }
  .contact__name {
    font-size: 35px;
    font-weight: 500;
    color: var(--name-blue);
    line-height: 1.2;
  }
  .contact__role {
    font-size: 24px;
    margin-top: 6px;
  }
  .contact__list {
    list-style: none;
    margin-top: 36px;
  }
  .contact__item {
    display: flex;
    align-items: center;
    height: 38.5px;
    font-size: 24px;
  }
  .contact__icon {
    width: 24px;
    height: 24px;
    margin-right: 22px;
    flex: none;
  }
</style>
</head>
<body>
<main class="canvas">
  <article class="card">
    <svg class="card__band" viewBox="0 0 1000 605" aria-hidden="true">
      <defs>
        <linearGradient id="bandBlue" x1="0" y1="0" x2="1" y2="1">
          <stop offset="0" stop-color="#2a8cc4"/>
          <stop offset="1" stop-color="#16689c"/>
        </linearGradient>
      </defs>
      <path d="M0 0 H430 C500 150 505 430 410 605 H0 Z" fill="var(--edge-dark)"/>
      <path d="M0 0 H412 C484 150 488 430 392 605 H0 Z" fill="url(#bandBlue)"/>
    </svg>

    <div class="brand">
      <span class="brand__mark"></span>
      <p class="brand__name">
        <span>Stonebridge</span>
        <span class="brand__sub">Building and Projects</span>
      </p>
    </div>

    <section class="contact">
      <h1 class="contact__name">Omar Haddani</h1>
      <p class="contact__role">Managing Director</p>
      <ul class="contact__list">
        <li class="contact__item">
          <svg class="contact__icon" viewBox="0 0 24 24" fill="none" stroke="var(--icon-ink)" stroke-width="1.8">
            <circle cx="12" cy="12" r="10"/>
            <path d="M8.5 7.5c-.8.8-.8 2.5.6 4.6 1.5 2.2 3.3 3.7 5 3.9.9.1 1.5-.4 1.9-1l-1.9-1.5-1.2.8c-1-.5-2.2-1.8-2.6-2.8l.8-1.2-1.4-2z" fill="var(--icon-ink)" stroke-width="1"/>
          </svg>
          <span>0400 318 276</span>
        </li>
        <li class="contact__item">
          <svg class="contact__icon" viewBox="0 0 24 24" fill="none" stroke="var(--icon-ink)" stroke-width="1.8">
            <rect x="3" y="5.5" width="18" height="13" rx="1.5"/>
            <path d="M3.5 6.5l8.5 6.5 8.5-6.5"/>
          </svg>
          <span>omar@sbpbuilding.com.au</span>
        </li>
        <li class="contact__item">
          <svg class="contact__icon" viewBox="0 0 24 24" fill="none" stroke="var(--icon-ink)" stroke-width="1.6">
            <circle cx="12" cy="12" r="9.5"/>
            <ellipse cx="12" cy="12" rx="4.2" ry="9.5"/>
            <path d="M2.5 12h19M4 7h16M4 17h16"/>
          </svg>
          <span>sbpbuilding.com.au</span>
        </li>
        <li class="contact__item">
          <svg class="contact__icon" viewBox="0 0 24 24" fill="none" stroke="var(--icon-ink)" stroke-width="1.8">
            <circle cx="12" cy="12" r="9"/>
          </svg>
          <span>sbp_building</span>
        </li>
      </ul>
    </section>
  </article>
</main>
</body>
</html>
```